Business Card For Halvenmoor Financial Consulting

Hi, I would like a business card designed. Bold, modern.
Please use the same design as the logo. I have also attached the website design to see the overall theme.
Wordmark Font
Color: Hex: #01AEF7

```html
<!DOCTYPE html>
<html lang="en">
<head>
<meta charset="utf-8">
<title>Halvenmoor Financial Consulting – Business Card</title>
<link rel="stylesheet" href="https://fonts.googleapis.com/css2?family=Open+Sans:wght@400;700;800&display=swap">
<style>
  :root {
    --canvas-bg: #222222;
    --card-navy: #0b466b;
    --card-navy-deep: #08395a;
    --card-navy-light: #125a87;
    --accent-blue: #01aef7;
    --text-white: #ffffff;
    --text-soft: #e3eef6;
  }
  * { box-sizing: border-box; margin: 0; padding: 0; }
  html, body {
    width: 1200px;
    height: 780px;
    overflow: hidden;
    background: var(--canvas-bg);
    font-family: "Open Sans", Arial, sans-serif;
  }
  .stage {
    position: relative;
    width: 1200px;
    height: 780px;
    display: flex;
    align-items: center;
    justify-content: center;
    gap: 50px;
  }
  .card {
    position: relative;
    width: 540px;
    height: 310px;
    background: var(--card-navy);
    overflow: hidden;
    color: var(--text-white);
  }

  /* Front */
  .brand {
    position: absolute;
    top: 30px;
    left: 30px;
    display: flex;
    align-items: center;
    gap: 10px;
  }
  .brand-square {
    width: 22px;
    height: 22px;
    border: 3px solid var(--accent-blue);
  }
  .brand-name {
    font-weight: 800;
    font-size: 17px;
    line-height: 1.15;
    letter-spacing: 0.5px;
    color: var(--text-white);
    text-transform: uppercase;
  }
  .address {
    position: absolute;
    left: 30px;
    top: 118px;
    font-size: 13px;
    line-height: 18px;
    color: var(--text-soft);
  }
  .contact-list {
    position: absolute;
    left: 30px;
    top: 162px;
    list-style: none;
    font-size: 13px;
    line-height: 20px;
    color: var(--text-soft);
  }
  .contact-list li {
    display: flex;
    align-items: center;
    gap: 8px;
  }
  .contact-list svg { width: 12px; height: 12px; fill: var(--accent-blue); flex: none; }
  .holder {
    position: absolute;
    right: 44px;
    top: 92px;
    text-align: right;
  }
  .holder-name {
    font-size: 22px;
    font-weight: 700;
    line-height: 1.1;
  }
  .holder-name .first { color: var(--accent-blue); }
  .holder-name .last { color: var(--text-white); }
  .holder-role {
    font-size: 14px;
    color: var(--text-soft);
    margin-top: 4px;
  }
  .accent-bar {
    position: absolute;
    right: 0;
    top: 98px;
    width: 22px;
    height: 34px;
    background: var(--accent-blue);
  }
  .front-emblem-area {
    position: absolute;
    left: 250px;
    top: 165px;
    width: 250px;
    height: 145px;
    background: linear-gradient(135deg, var(--card-navy-deep), var(--card-navy-light));
    box-shadow: inset 0 0 0 1px rgba(255,255,255,0.06);
  }

  /* Back */
  .back-pattern-area {
    position: absolute;
    inset: 0;
    background: linear-gradient(135deg, var(--card-navy-deep), var(--card-navy) 50%, var(--card-navy-light));
  }
  .back-brand {
    position: absolute;
    inset: 0;
    display: flex;
    align-items: center;
    justify-content: center;
    gap: 12px;
  }
  .back-brand .brand-square { width: 30px; height: 30px; border-width: 4px; }
  .back-brand .brand-name { font-size: 22px; }
</style>
</head>
<body>
<main class="stage">
  <section class="card card-front" aria-label="Business card front">
    <div class="brand">
      <span class="brand-square"></span>
      <span class="brand-name">Halvenmoor<br>Financial Consulting</span>
    </div>

    <p class="address">418 Cedarline Ave. Suite 310<br>Riverton, TX 75011</p>

    <ul class="contact-list">
      <li>
        <svg viewBox="0 0 24 24" aria-hidden="true"><path d="M6.6 10.8a15.1 15.1 0 0 0 6.6 6.6l2.2-2.2a1 1 0 0 1 1-.25 11.4 11.4 0 0 0 3.6.57 1 1 0 0 1 1 1V20a1 1 0 0 1-1 1A17 17 0 0 1 3 4a1 1 0 0 1 1-1h3.5a1 1 0 0 1 1 1c0 1.25.2 2.45.57 3.57a1 1 0 0 1-.25 1z"/></svg>
        (555) 214-6093
      </li>
      <li>
        <svg viewBox="0 0 24 24" aria-hidden="true"><path d="M2 5h20v14H2z M4 7v.5l8 5 8-5V7l-8 5z" fill-rule="evenodd"/></svg>
        info@halvenmoor.com
      </li>
      <li>
        <svg viewBox="0 0 24 24" aria-hidden="true"><circle cx="12" cy="12" r="10"/></svg>
        www.halvenmoor.com
      </li>
    </ul>

    <div class="holder">
      <p class="holder-name"><span class="first">Mirela</span> <span class="last">Dovanska</span></p>
      <p class="holder-role">Managing Director</p>
    </div>
    <span class="accent-bar"></span>

    <div class="front-emblem-area" role="img" aria-label="Large embossed brand emblem"></div>
  </section>

  <section class="card card-back" aria-label="Business card back">
    <div class="back-pattern-area" role="img" aria-label="Repeating embossed brand emblem pattern"></div>
    <div class="back-brand">
      <span class="brand-square"></span>
      <span class="brand-name">Halvenmoor<br>Financial Consulting</span>
    </div>
  </section>
</main>
</body>
</html>
```